real esate business card with company logo and name

we need a business card design for a real esate company

The company name is Walsh & Brand Pty Ltd, and we have our logo designed and will upload. We want classic or moden feel. Black or white background. looks more textured. Should include folowinginformations
Owen Walsh and Lucy Brand
Sales Agents & Onsite Manager
p: 07 5948 2063
F: 07 5948 2174
M:0431 857 219
3/42 Marlow Crescent, FERNLEA QLD 4213

We want this business card looks professonal. Thank you in advance.

Industry/Entity Type

Real Estate Agent

Contact Information for Business Card

Owen Walsh and Lucy Brand
Onsite Manager & Sales Agents
p: 07 5948 2063
M:0431 857 219

Font styles to use
Serif

Colors
000000
fbfbfb
333333
959595

Requirements
Must have
• company logo and name, black or white back ground

```html
<!DOCTYPE html>
<html lang="en">
<head>
<meta charset="utf-8">
<title>Walsh &amp; Brand Pty Ltd — Business Card</title>
<link href="https://fonts.googleapis.com/css2?family=Source+Sans+3:wght@400;600&display=swap" rel="stylesheet">
<style>
  :root {
    --stage: #3a3a3a;
    --paper: #fbfbfb;
    --charcoal: #333333;
    --ink: #444444;
    --muted: #959595;
    --rule: #555555;
    --tab: #e6e6e6;
    --dark-card: #4a4a4a;
    --white: #ffffff;
  }
  * { margin: 0; padding: 0; box-sizing: border-box; }
  html, body {
    width: 1200px; height: 750px; overflow: hidden;
    background: var(--stage);
    font-family: "Source Sans 3", sans-serif;
  }
  .canvas { position: relative; width: 1200px; height: 750px; }
  .card {
    position: absolute; top: 228px;
    width: 462px; height: 263px;
    overflow: hidden;
  }
  .card--front { left: 124px; background: var(--paper); }
  .card--back { left: 618px; background: var(--dark-card); }

  .brand-tab {
    position: absolute; left: 321px; top: 0;
    width: 97px; height: 120px;
    background: var(--tab);
  }
  .brand-tab__mark {
    position: absolute; left: 28px; top: 38px;
    width: 41px; height: 41px; background: var(--muted);
  }
  .front__company {
    position: absolute; right: 28px; top: 126px;
    font-size: 11px; font-weight: 600; letter-spacing: 0.6px;
    color: var(--charcoal); text-transform: uppercase;
  }
  .front__names {
    position: absolute; left: 26px; top: 147px;
    font-size: 17px; font-weight: 600; color: var(--ink);
  }
  .front__role {
    position: absolute; left: 26px; top: 168px;
    font-size: 12px; color: var(--muted);
  }
  .front__rule {
    position: absolute; left: 26px; top: 189px;
    width: 408px; height: 1px; background: var(--rule);
  }
  .contact-list {
    position: absolute; left: 26px; top: 197px;
    list-style: none;
  }
  .contact-list li {
    display: flex; align-items: center; gap: 6px;
    height: 17.5px; font-size: 11px; color: var(--ink);
  }
  .contact-list svg { width: 11px; height: 11px; fill: var(--ink); }
  .front__address {
    position: absolute; right: 28px; top: 216px;
    font-size: 11px; line-height: 16px; color: var(--ink);
    text-align: right; font-style: normal;
  }

  .back__mark {
    position: absolute; left: 199px; top: 74px;
    width: 64px; height: 64px; background: var(--white);
  }
  .back__company {
    position: absolute; left: 0; right: 0; top: 156px;
    text-align: center;
    font-size: 11.5px; font-weight: 600; letter-spacing: 0.6px;
    color: var(--white); text-transform: uppercase;
  }
</style>
</head>
<body>
<main class="canvas">
  <section class="card card--front" aria-label="Card front">
    <div class="brand-tab"><div class="brand-tab__mark"></div></div>
    <p class="front__company">Walsh &amp; Brand Pty Ltd.</p>
    <h1 class="front__names">Owen Walsh &amp; Lucy Brand</h1>
    <p class="front__role">Sales Agents &amp; Onsite Manager</p>
    <div class="front__rule"></div>
    <ul class="contact-list">
      <li>
        <svg viewBox="0 0 24 24" aria-hidden="true"><path d="M6.6 10.8a15 15 0 0 0 6.6 6.6l2.2-2.2c.3-.3.7-.4 1-.2 1.1.4 2.3.6 3.6.6.6 0 1 .4 1 1V20c0 .6-.4 1-1 1A17 17 0 0 1 3 4c0-.6.4-1 1-1h3.5c.6 0 1 .4 1 1 0 1.3.2 2.5.6 3.6.1.3 0 .7-.2 1z"/></svg>
        07 5948 2063
      </li>
      <li>
        <svg viewBox="0 0 24 24" aria-hidden="true"><path d="M7 1h10a2 2 0 0 1 2 2v18a2 2 0 0 1-2 2H7a2 2 0 0 1-2-2V3a2 2 0 0 1 2-2zm0 3v14h10V4zm5 15.5a1.2 1.2 0 1 0 0 2.4 1.2 1.2 0 0 0 0-2.4z"/></svg>
        0431 857 219
      </li>
      <li>
        <svg viewBox="0 0 24 24" aria-hidden="true"><path d="M6 2h10l2 2v5H6zM3 10h18a2 2 0 0 1 2 2v8H1v-8a2 2 0 0 1 2-2zm3 5v2h12v-2z"/></svg>
        07 5948 2174
      </li>
    </ul>
    <address class="front__address">3/42 Marlow Crescent<br>FERNLEA QLD 4213</address>
  </section>

  <section class="card card--back" aria-label="Card back">
    <div class="back__mark"></div>
    <p class="back__company">Walsh &amp; Brand Pty Ltd.</p>
  </section>
</main>
</body>
</html>
```